New Stationary and Logo Design for Start Up Company

We need a logo design and stationary set including letterhead, business card (double sided), compliments slip and envelope for a new company Bright Harbour Media.
The files should be editable to update address and standard contact details, will need to forward to web designer and stationary printer.
The company will be an online marketer and distributer of various business education products in Australia.
The designs should convey simple clean image
Target Market(s)
Small business owners and professional service providers (ie Accountants, Lawyers, Real Estate Agents) in Australia
Industry/Entity Type
Education
Look and feel
Each slider illustrates characteristics of the customer's brand and the style your logo design should communicate.

```html
<!DOCTYPE html>
<html lang="en">
<head>
<meta charset="utf-8">
<title>Bright Harbour Media – Envelope</title>
<link rel="stylesheet" href="https://fonts.googleapis.com/css2?family=Roboto:wght@300;400;700&display=swap">
<style>
  :root {
    --paper: #ffffff;
    --stage: #ffffff;
    --slate: #4a5660;
    --ink: #3b4249;
    --muted: #6b7278;
    --accent: #1a9ad6;
    --fold: #d9dcdf;
    --shadow: rgba(0, 0, 0, 0.28);
  }
  * { box-sizing: border-box; margin: 0; padding: 0; }
  html, body {
    width: 1200px;
    height: 366px;
    overflow: hidden;
    background: var(--stage);
    font-family: "Roboto", Arial, sans-serif;
  }
  .canvas {
    position: relative;
    width: 1200px;
    height: 366px;
  }
  .envelope {
    position: absolute;
    top: 36px;
    width: 572px;
    height: 290px;
    background: var(--paper);
    box-shadow: 2px 4px 8px var(--shadow);
  }
  .envelope--back { left: 26px; }
  .envelope--front { left: 604px; }
  .envelope__flap {
    position: absolute;
    inset: 0;
    width: 100%;
    height: 100%;
  }
  .brand {
    position: absolute;
    top: 16px;
    left: 18px;
    display: flex;
    align-items: center;
    gap: 6px;
  }
  .brand__mark {
    width: 7px;
    height: 7px;
    background: var(--accent);
  }
  .brand__name {
    font-size: 16px;
    font-weight: 400;
    letter-spacing: -0.4px;
    color: var(--slate);
  }
  .contact {
    position: absolute;
    right: 40px;
    bottom: 22px;
    display: flex;
    gap: 6px;
  }
  .contact__bracket {
    width: 5px;
    border: 2px solid var(--accent);
    border-right: none;
  }
  .contact__list {
    list-style: none;
    font-size: 7px;
    line-height: 8.5px;
    color: var(--muted);
    font-weight: 300;
  }
  .contact__label {
    font-weight: 700;
    color: var(--ink);
  }
</style>
</head>
<body>
<main class="canvas">
  <section class="envelope envelope--back" aria-label="Envelope back">
    <svg class="envelope__flap" viewBox="0 0 572 290" preserveAspectRatio="none" aria-hidden="true">
      <line x1="0" y1="290" x2="225" y2="128" stroke="var(--fold)" stroke-width="1"/>
      <line x1="572" y1="290" x2="350" y2="122" stroke="var(--fold)" stroke-width="1"/>
      <polygon points="0,0 572,0 288,162" fill="var(--slate)"/>
    </svg>
  </section>

  <section class="envelope envelope--front" aria-label="Envelope front">
    <div class="brand">
      <span class="brand__mark"></span>
      <span class="brand__name">Bright Harbour Media</span>
    </div>
    <address class="contact">
      <span class="contact__bracket"></span>
      <ul class="contact__list">
        <li><span class="contact__label">adress:</span> 218 Harbour Lane</li>
        <li><span class="contact__label">tel:</span> 954.555.0147</li>
        <li><span class="contact__label">e-mail:</span> info@brightharbour.com.au</li>
        <li><span class="contact__label">web:</span> www.brightharbour.com.au</li>
      </ul>
    </address>
  </section>
</main>
</body>
</html>
```